Local fast-growing company in the service sector

We are looking for a modern business card design, which should also appear on our letterheads

Target Market(s)

Private and industrial sectors

Contact Information for Business Card

Vorname Name
Kellberger Str. 18
72458 Tannfeld
Tel.: 07146-839214-0
Name@agentur-kvtl.de

Colors
9d9d9d
919191
aaaaaa

Requirements
Must have
• The logo (file) in silver

```html
<!DOCTYPE html>
<html lang="de">
<head>
<meta charset="utf-8">
<title>KVTL Visitenkarte</title>
<link href="https://fonts.googleapis.com/css2?family=Montserrat:wght@400;500;700&family=Michroma&display=swap" rel="stylesheet">
<style>
  :root {
    --backdrop: #3a3a3a;
    --card: #1c1c1d;
    --silver: #aaaaaa;
    --silver-mid: #9d9d9d;
    --silver-dark: #919191;
    --text-light: #e6e6e6;
  }
  * { margin: 0; padding: 0; box-sizing: border-box; }
  html, body {
    width: 799px;
    height: 1200px;
    overflow: hidden;
    background: var(--backdrop);
  }
  .sheet {
    width: 799px;
    height: 1200px;
    display: flex;
    flex-direction: column;
    align-items: center;
    justify-content: center;
    gap: 70px;
  }
  .card {
    position: relative;
    width: 660px;
    height: 380px;
    background: var(--card);
    border-radius: 4px;
    font-family: "Montserrat", sans-serif;
  }

  /* Front */
  .card-front {
    display: flex;
    align-items: center;
    justify-content: center;
    gap: 18px;
  }
  .front-mark {
    width: 34px;
    height: 34px;
    border-radius: 50%;
    background: var(--silver-dark);
  }
  .front-name {
    font-weight: 700;
    font-size: 74px;
    letter-spacing: 4px;
    color: var(--silver-dark);
  }

  /* Back */
  .holder-name {
    position: absolute;
    left: 40px;
    top: 44px;
    font-family: "Michroma", sans-serif;
    font-size: 17px;
    letter-spacing: 3px;
    color: var(--silver-mid);
  }
  .contact {
    position: absolute;
    left: 40px;
    bottom: 54px;
    list-style: none;
    color: var(--text-light);
    font-size: 15px;
    line-height: 25px;
  }
  .contact li { display: flex; align-items: center; gap: 10px; }
  .contact .icon { width: 13px; height: 13px; fill: var(--text-light); flex: none; }
  .contact .address { margin-top: 2px; }
  .brand {
    position: absolute;
    right: 44px;
    bottom: 70px;
    display: flex;
    flex-direction: column;
    align-items: flex-end;
  }
  .brand-name {
    font-weight: 700;
    font-size: 56px;
    line-height: 1;
    letter-spacing: 2px;
    color: var(--silver);
  }
  .brand-web {
    font-weight: 700;
    font-size: 20px;
    letter-spacing: 1px;
    color: var(--silver);
    margin-top: 4px;
  }
</style>
</head>
<body>
<main class="sheet">
  <section class="card card-front" aria-label="Vorderseite">
    <span class="front-mark"></span>
    <span class="front-name">KVTL</span>
  </section>

  <section class="card card-back" aria-label="Rückseite">
    <p class="holder-name">VORNAME NAME</p>
    <ul class="contact">
      <li>
        <svg class="icon" viewBox="0 0 16 16" aria-hidden="true"><path d="M3 1l3 3-2 2c1 2 3 4 5 5l2-2 3 3-2 3C7 15 1 9 0 4z"/></svg>
        07146-839214-0
      </li>
      <li>
        <svg class="icon" viewBox="0 0 16 16" aria-hidden="true"><path d="M0 3h16v10H0z M1.5 4.5L8 9l6.5-4.5" stroke="#1c1c1d" stroke-width="1.4"/></svg>
        Name@agentur-kvtl.de
      </li>
      <li>
        <svg class="icon" viewBox="0 0 16 16" aria-hidden="true"><circle cx="8" cy="8" r="7.5"/><path d="M0.5 8h15M8 0.5v15M8 0.5c-4 4-4 11 0 15M8 0.5c4 4 4 11 0 15" stroke="#1c1c1d" stroke-width="1.1" fill="none"/></svg>
        www.agentur-kvtl.de
      </li>
      <li class="address">Kellberger Str. 18 72458 Tannfeld</li>
    </ul>
    <div class="brand">
      <span class="brand-name">KVTL</span>
      <span class="brand-web">agentur-kvtl.de</span>
    </div>
  </section>
</main>
</body>
</html>
```